Plotvista Caribbean

We need a vibrant, user friendly and exciting website for our land search company called "plotVista" This application will help individuals locate and or list lots for sale within the Caribbean. We will offer a small cash back incentive to buyers that purchase land from our site, and we will charge a 1%-2% success fee to our sellers once a successful transaction is made. We would like to become a match making site, matching buyers and sellers on our platform. We will also include a service directory and marketing advertisement spot for other service providers for a fee. We would like to see a webdesign incorporating Caribbean colors (blue, green and yellow) with very modern clean lines, very picturesque and easy to use.

Industry/Entity Type

Real Estate

Coding

Coded - Design and coding required

Number of Pages Required

5+ page

Font styles to use
Sans Serif

Colors
ffffff
85acd3
b768aa
dbdbdb

Requirements
Nice to have
• Scenic photos of the ocean and beautiful landscape

```html
<!DOCTYPE html>
<html lang="en">
<head>
<meta charset="utf-8">
<title>plotVista – Land for sale in the Caribbean</title>
<link rel="stylesheet" href="https://fonts.googleapis.com/css2?family=Nunito+Sans:wght@400;600;700&family=Open+Sans:wght@400;600;700&display=swap">
<style>
:root{
  --white:#ffffff;
  --sky:#85acd3;
  --orchid:#b768aa;
  --mist:#dbdbdb;
  --ink:#1c1c1c;
  --text:#555a60;
  --footer:#0d0d0d;
  --sea-deep:#0f3f6b;
  --sea-mid:#1f6f8f;
  --land:#3f6a35;
}
*{margin:0;padding:0;box-sizing:border-box}
html,body{width:1200px;height:2671px;overflow:hidden;background:var(--white)}
body{position:relative;font-family:"Open Sans",Arial,sans-serif;color:var(--text)}
.abs{position:absolute}
h1,h2,h3,.brand{font-family:"Nunito Sans",Arial,sans-serif}

/* Hero */
.hero{left:0;top:0;width:1200px;height:507px;
  background:linear-gradient(180deg,#2a4a6a 0%,#1d5a8a 25%,var(--sea-deep) 45%,#1d6a82 65%,var(--land) 85%,#4d7440 100%)}
.brand{left:98px;top:30px;font-size:30px;font-weight:600;color:var(--white)}
.top-phone{right:85px;top:12px;display:flex;align-items:center;gap:12px;color:var(--white);font-size:17px;font-weight:600}
.top-phone .ring{width:30px;height:30px;border:1.5px solid var(--white);border-radius:50%;display:flex;align-items:center;justify-content:center}
.main-nav{right:93px;top:56px;display:flex;gap:35px;font-size:16px;font-weight:600;color:var(--white);align-items:center}
.main-nav .active{color:var(--orchid)}
.hero-title{left:0;width:1200px;top:128px;text-align:center;font-size:66px;font-weight:600;color:var(--white)}
.hero-sub{left:0;width:1200px;top:219px;text-align:center;font-size:23px;font-weight:600;color:var(--white)}
.search{left:308px;top:280px;width:584px;height:49px;display:flex}
.search-field{flex:1;background:var(--white);font-size:14px;color:#777;padding:0 20px;display:flex;align-items:center}
.search-btn{width:128px;background:var(--orchid);color:var(--white);font-weight:700;font-size:16px;display:flex;align-items:center;justify-content:center;letter-spacing:.5px}
.dots{left:568px;top:446px;display:flex;gap:4px}
.dots span{width:12px;height:12px;border:1.5px solid var(--white);border-radius:50%}
.dots span.on{background:var(--white)}

/* Welcome */
.welcome-title{left:98px;top:556px;font-size:30px;font-weight:600;color:var(--ink)}
.welcome-copy{left:98px;top:620px;width:500px;font-size:12.5px;line-height:25px;color:var(--text)}
.welcome-copy p+p{margin-top:28px}
.btn-outline{border:1.5px solid var(--orchid);border-radius:22px;color:var(--orchid);font-size:13px;font-weight:700;display:flex;align-items:center;justify-content:center;letter-spacing:.5px}
.read-more{left:98px;top:822px;width:128px;height:36px}
.video-frame{left:646px;top:566px;width:456px;height:294px;border:2px solid var(--mist);padding:4px;background:var(--white)}
.video-still{width:100%;height:100%;background:linear-gradient(135deg,#7fd6d6 0%,#33b3c4 35%,#c9c2b2 60%,#5f8c4b 85%,#3f6b35 100%);position:relative}
.play{position:absolute;left:50%;top:50%;width:58px;height:58px;margin:-29px 0 0 -29px;border-radius:50%;background:rgba(20,20,20,.75);display:flex;align-items:center;justify-content:center}

/* Incentive band */
.band{left:0;top:922px;width:1200px;height:289px;
  background:linear-gradient(180deg,#4a6a48 0%,#2f7f86 30%,#1f6f7c 60%,#145a6a 100%)}
.band-text{left:130px;top:995px;width:940px;text-align:center;font-size:27px;line-height:41px;font-weight:600;color:var(--white);font-family:"Nunito Sans",Arial,sans-serif}

/* Services */
.section-title{left:0;width:1200px;text-align:center;font-size:30px;font-weight:600;color:var(--ink)}
.service{width:240px;text-align:center}
.service svg{display:block;margin:0 auto}
.service h3{font-size:20px;font-weight:600;color:var(--ink);margin-top:20px}
.service p{font-size:12.5px;line-height:25px;color:var(--text);margin-top:6px;padding:0 8px}
.rule{left:98px;top:1684px;width:1004px;height:1px;background:var(--mist)}

/* Destinations */
.dest{background:linear-gradient(160deg,#5ea8cf,#2b8fa8)}
.dest-main{left:98px;top:1820px;width:621px;height:454px;background:linear-gradient(180deg,#6fa6c9 0%,#2a7ea0 20%,#4d8a4a 45%,#e8e2d2 75%,#7ed3cf 100%)}
.dest-top{left:725px;top:1820px;width:377px;height:224px;background:linear-gradient(180deg,#9fc2e0 0%,#e8eef4 25%,#4d7a4a 55%,#37a9b7 80%,#2f6b3a 100%)}
.dest-bottom{left:725px;top:2049px;width:377px;height:225px;background:linear-gradient(180deg,#c2d6e8 0%,#7f9fb8 25%,#3e6a3a 50%,#1f7a8f 80%,#4a7a3a 100%)}
.explore{left:507px;top:2320px;width:186px;height:44px}

/* Footer */
.footer{left:0;top:2439px;width:1200px;height:232px;background:var(--footer);color:var(--white)}
.contact-item{display:flex;align-items:center;gap:16px;font-size:14px;line-height:22px}
.ring-lg{width:42px;height:42px;border:1.5px solid var(--white);border-radius:50%;display:flex;align-items:center;justify-content:center;flex:none}
.footer-nav{left:0;width:1200px;top:2550px;display:flex;justify-content:center;gap:0;font-size:14px}
.footer-nav span{padding:0 18px}
.footer-nav .sep{padding:0}
.footer-rule{left:98px;top:2603px;width:1004px;height:1px;background:#2e2e2e}
.copyright{left:98px;top:2628px;font-size:13px}
.social{left:945px;top:2619px;display:flex;gap:10px}
.social span{width:32px;height:32px;border:1.5px solid var(--white);border-radius:50%}
</style>
</head>
<body>

<header>
  <div class="abs hero" role="img" aria-label="Aerial photo of green Caribbean islands in a deep blue sea with sailboats"></div>
  <div class="abs brand">plotVista</div>
  <div class="abs top-phone">
    <span class="ring"><svg width="14" height="14" viewBox="0 0 24 24"><path d="M6.6 10.8a15 15 0 0 0 6.6 6.6l2.2-2.2a1 1 0 0 1 1-.25 11.4 11.4 0 0 0 3.6.6 1 1 0 0 1 1 1V20a1 1 0 0 1-1 1A17 17 0 0 1 3 4a1 1 0 0 1 1-1h3.5a1 1 0 0 1 1 1c0 1.25.2 2.45.6 3.6a1 1 0 0 1-.25 1z" fill="#fff"/></svg></span>
    1 800 555 0142
  </div>
  <nav class="abs main-nav">
    <span class="active">Home</span><span>About</span><span>Buy</span><span>Sell</span><span>Landlords</span><span>Rent</span><span>Our services</span><span>Contact</span>
    <svg width="16" height="16" viewBox="0 0 24 24"><circle cx="10" cy="10" r="7" fill="none" stroke="#fff" stroke-width="3"/><line x1="15" y1="15" x2="22" y2="22" stroke="#fff" stroke-width="3"/></svg>
  </nav>
  <h1 class="abs hero-title">plotVista</h1>
  <p class="abs hero-sub">We help individuals locate and or list lots for sale within the Caribbean.</p>
  <div class="abs search">
    <div class="search-field">Enter Town or Post Code</div>
    <div class="search-btn">SEARCH</div>
  </div>
  <div class="abs dots"><span class="on"></span><span></span><span></span><span></span></div>
</header>

<section class="welcome">
  <h2 class="abs welcome-title">Welcome to plotVista</h2>
  <div class="abs welcome-copy">
    <p>We connect buyers and sellers of land across the islands, making every search for the right lot simple, clear and quick.</p>
    <p>Browse verified listings from trusted local owners, compare prices by town or parish, and reach sellers directly through our platform. Our team guides you from the first search to the final signature, so every step of your purchase or sale stays easy, transparent and secure for everyone involved.</p>
  </div>
  <div class="abs btn-outline read-more">READ MORE &gt;&gt;</div>
  <div class="abs video-frame">
    <div class="video-still" role="img" aria-label="Video still: aerial view of a turquoise bay lined with white resort buildings">
      <span class="play"><svg width="20" height="22" viewBox="0 0 20 22"><path d="M3 2l15 9-15 9z" fill="#fff"/></svg></span>
    </div>
  </div>
</section>

<section>
  <div class="abs band" role="img" aria-label="Photo of a calm teal harbour with wooden piers and a green shoreline"></div>
  <p class="abs band-text">We will offer a small cash back incentive to buyers that purchase land from our site, and we will charge a 1%-2% success fee to our sellers once a successful transaction is made.</p>
</section>

<section class="services">
  <h2 class="abs section-title" style="top:1266px">Our Services</h2>

  <div class="abs service" style="left:76px;top:1350px">
    <svg width="180" height="180" viewBox="0 0 180 180">
      <rect x="33" y="33" width="114" height="114" transform="rotate(45 90 90)" fill="none" stroke="var(--orchid)" stroke-width="1.5"/>
      <rect x="40" y="40" width="100" height="100" transform="rotate(45 90 90)" fill="var(--orchid)"/>
      <rect x="66" y="77" width="48" height="28" rx="2" fill="#fff"/>
      <rect x="71" y="82" width="38" height="18" fill="var(--orchid)"/>
      <circle cx="90" cy="91" r="7" fill="#fff"/>
    </svg>
    <h3>Buy</h3>
    <p>Find the perfect lot for your future island home today</p>
  </div>

  <div class="abs service" style="left:343px;top:1350px">
    <svg width="180" height="180" viewBox="0 0 180 180">
      <rect x="33" y="33" width="114" height="114" transform="rotate(45 90 90)" fill="none" stroke="var(--orchid)" stroke-width="1.5"/>
      <rect x="40" y="40" width="100" height="100" transform="rotate(45 90 90)" fill="#fff" stroke="var(--orchid)" stroke-width="3"/>
      <path d="M70 78h7l6 22h20l5-16H80" fill="none" stroke="var(--sky)" stroke-width="4" stroke-linejoin="round"/>
      <circle cx="86" cy="106" r="3.5" fill="var(--sky)"/><circle cx="100" cy="106" r="3.5" fill="var(--sky)"/>
    </svg>
    <h3>Sell</h3>
    <p>List your land and reach serious buyers across the region</p>
  </div>

  <div class="abs service" style="left:610px;top:1350px">
    <svg width="180" height="180" viewBox="0 0 180 180">
      <rect x="33" y="33" width="114" height="114" transform="rotate(45 90 90)" fill="none" stroke="var(--orchid)" stroke-width="1.5"/>
      <rect x="40" y="40" width="100" height="100" transform="rotate(45 90 90)" fill="#fff" stroke="var(--orchid)" stroke-width="3"/>
      <path d="M78 84l12-12 12 12" fill="none" stroke="var(--sky)" stroke-width="2"/>
      <circle cx="90" cy="72" r="2.5" fill="var(--sky)"/>
      <rect x="68" y="84" width="44" height="22" rx="2" fill="var(--sky)"/>
      <text x="90" y="100" text-anchor="middle" font-family="Open Sans, sans-serif" font-size="11" font-weight="700" fill="#fff">RENT</text>
    </svg>
    <h3>Rent</h3>
    <p>Lease plots and properties for short or long term stays</p>
  </div>

  <div class="abs service" style="left:877px;top:1350px">
    <svg width="180" height="180" viewBox="0 0 180 180">
      <rect x="33" y="33" width="114" height="114" transform="rotate(45 90 90)" fill="none" stroke="var(--orchid)" stroke-width="1.5"/>
      <rect x="40" y="40" width="100" height="100" transform="rotate(45 90 90)" fill="#fff" stroke="var(--orchid)" stroke-width="3"/>
      <ellipse cx="85" cy="86" rx="13" ry="9" fill="none" stroke="var(--sky)" stroke-width="3"/>
      <path d="M78 94l-4 6 8-3" fill="var(--sky)"/>
      <path d="M96 82a12 8 0 0 1 4 15l3 5-7-3" fill="none" stroke="var(--sky)" stroke-width="3"/>
    </svg>
    <h3>Consulting</h3>
    <p>Get expert advice on pricing, permits and local markets</p>
  </div>

  <div class="abs rule"></div>
</section>

<section class="destinations">
  <h2 class="abs section-title" style="top:1735px">Featured Destinations</h2>
  <div class="abs dest-main" role="img" aria-label="Aerial photo of a white beach resort with palm trees and turquoise water"></div>
  <div class="abs dest-top" role="img" aria-label="Photo of a hilly island town beside a turquoise bay"></div>
  <div class="abs dest-bottom" role="img" aria-label="Photo of a green cove with anchored boats and a sandy beach"></div>
  <div class="abs btn-outline explore">EXPLORE MORE</div>
</section>

<footer>
  <div class="abs footer"></div>
  <div class="abs contact-item" style="left:288px;top:2476px;color:#fff">
    <span class="ring-lg"><svg width="14" height="18" viewBox="0 0 14 18"><path d="M7 0a7 7 0 0 0-7 7c0 5 7 11 7 11s7-6 7-11a7 7 0 0 0-7-7z" fill="#fff"/><circle cx="7" cy="7" r="2.5" fill="#0d0d0d"/></svg></span>
    <span>214 Harbour View Road<br>Bridgetown, BB 11000</span>
  </div>
  <div class="abs contact-item" style="left:518px;top:2476px;color:#fff">
    <span class="ring-lg"><svg width="16" height="16" viewBox="0 0 24 24"><path d="M6.6 10.8a15 15 0 0 0 6.6 6.6l2.2-2.2a1 1 0 0 1 1-.25 11.4 11.4 0 0 0 3.6.6 1 1 0 0 1 1 1V20a1 1 0 0 1-1 1A17 17 0 0 1 3 4a1 1 0 0 1 1-1h3.5a1 1 0 0 1 1 1c0 1.25.2 2.45.6 3.6a1 1 0 0 1-.25 1z" fill="#fff"/></svg></span>
    <span>1 800 555 0142</span>
  </div>
  <div class="abs contact-item" style="left:723px;top:2476px;color:#fff">
    <span class="ring-lg"><svg width="18" height="14" viewBox="0 0 18 14"><rect width="18" height="14" rx="2" fill="#fff"/><path d="M1 1l8 7 8-7" fill="none" stroke="#0d0d0d" stroke-width="1.5"/></svg></span>
    <span>info@plotvista.com</span>
  </div>
  <nav class="abs footer-nav" style="color:#fff">
    <span>Home</span><span class="sep">|</span><span>About</span><span class="sep">|</span><span>Buy</span><span class="sep">|</span><span>Sell</span><span class="sep">|</span><span>Landlords</span><span class="sep">|</span><span>Rent</span><span class="sep">|</span><span>Our services</span><span class="sep">|</span><span>Contact</span>
  </nav>
  <div class="abs footer-rule"></div>
  <p class="abs copyright" style="color:#fff">Copyrights © 2017, plotVista . All rights reserved.</p>
  <div class="abs social" aria-label="Social links"><span></span><span></span><span></span><span></span></div>
</footer>

</body>
</html>
```